Pemberlux: Smart Quotes for Wine Lovers

Hello. I am completing book of quotes for wine lovers. Need the text formatted so that it is easy to read and aesthetically pleasing...modern, clean, smart. Number the pages. The cover is complete. Book is small square. 7.5 by 7.5 inches. If you want to show me first few pages that would be awesome. Thank you!
Updates

I edited the quotes so if you downloaded first ones, please grab these ones instead, thank you! 

Target Market(s)

wine lovers. Urban. Modern.

Industry/Entity Type

Quotes

Requirements
Should not have
• No color. black and white only.

```html
<!DOCTYPE html>
<html lang="en">
<head>
<meta charset="utf-8">
<title>Pemberlux: Smart Quotes for Wine Lovers</title>
<link rel="stylesheet" href="https://fonts.googleapis.com/css2?family=Jost:wght@300;400;500&display=swap">
<style>
  :root {
    --backdrop: #dcdcdc;
    --paper: #ffffff;
    --ink: #111111;
    --rule: #3a3a3a;
    --art-dark: #d0d0d0;
    --art-light: #ececec;
  }
  * { margin: 0; padding: 0; box-sizing: border-box; }
  html, body {
    width: 1200px; height: 900px; overflow: hidden;
    background: var(--backdrop);
    font-family: "Jost", "Futura", sans-serif;
    color: var(--ink);
  }
  .spread {
    position: absolute; left: 61px; top: 183px;
    width: 1074px; height: 534px;
    display: flex;
    border: 1px solid var(--rule);
    background: var(--paper);
  }
  .page { position: relative; width: 537px; height: 100%; }
  .page + .page { border-left: 1px solid var(--rule); }
  .quote {
    position: absolute; left: 30px; right: 30px; top: 51px;
    text-align: center;
    font-size: 27px; line-height: 35px; font-weight: 300;
  }
  .page-art {
    position: absolute; left: 50%; top: 213px;
    width: 70px; height: 170px; margin-left: -35px;
    background: linear-gradient(135deg, var(--art-light) 0%, var(--art-dark) 100%);
  }
  .author {
    position: absolute; left: 20px; right: 20px; bottom: 57px;
    text-align: center;
    font-size: 12.5px; line-height: 17.7px; font-weight: 400;
  }
  .author-name { font-weight: 500; }
  .page-number {
    position: absolute; left: 0; right: 0; bottom: 24px;
    text-align: center; font-size: 12.5px;
  }
</style>
</head>
<body>
  <main class="spread">
    <section class="page">
      <p class="quote">The discovery of a good wine is<br>increasingly better for mankind than the<br>discovery of a new star.<br>– Lorenzo Vellani</p>
      <div class="page-art" role="img" aria-label="Small grey illustration of two wine glasses"></div>
      <p class="author"><span class="author-name">Lorenzo Aldo Vellani</span> (1461 –1527)<br>Tuscan Vintner, Poet, Cellar Master, Traveller, Botanist,<br>Cook, Mapmaker, Storyteller, Letter Writer,<br>Gardener and Host.</p>
      <p class="page-number">1</p>
    </section>
    <section class="page">
      <p class="quote">Be careful to trust a person who<br>does not like wine.<br>– Konrad Maier</p>
      <div class="page-art" role="img" aria-label="Small grey illustration of two wine glasses"></div>
      <p class="author"><span class="author-name">Konrad Emil Maier</span> (1824 –1889)<br>Bavarian Brewer, Essayist, Innkeeper, Teacher, Traveller,<br>and Keen Amateur Winemaker.</p>
      <p class="page-number">2</p>
    </section>
  </main>
</body>
</html>
```